A Vegan Nutritional Supplement (one Product) website

I am looking for an experienced Web designer to build a One Product website for a Nutritional Supplement that is 100% vegan. The emphasis would be on both the Quality and Quantity of the ingredients and their benefits. It contains Essential Vitamins, Minerals, and a proprietary blend of 42 Fruits and Vegetables. I welcome color suggestions as long as it includes Green (vegan) and White.. The final design should communicate to the buyer: Quality, Healthy, Safety (Natural vegan ingredients), Natural energy, well being. The product includes benefits for 3 vital elements of optimal health: Immune Health, Heart Health, and Brain Health

Industry/Entity Type

Health and Wellness - Nutritional Supplements

Number of Pages Required

4 page

Other font styles liked:
• I Welcome your creativity

Colors
59FF00
82FF00
B8FF75
E3FFCB
F4FFEA

Requirements
Must have
• Options to purchase : One product ($34.95); 2 products ($31.45 each - 10% discount), or 3 Products ($27.95 each - 20% discount)
Nice to have
• Focus on the Benefits of having all these Ingredients - Nutrients in one bottle - Essential Vitamins, Minerals, and proprietary blend of 42 Fruits and Vegetables.

```html
<!DOCTYPE html>
<html lang="en">
<head>
<meta charset="utf-8">
<title>Leafwell Verdant Vigor</title>
<link href="https://fonts.googleapis.com/css2?family=Poppins:wght@400;500;600;700;800&family=Playball&display=swap" rel="stylesheet">
<style>
:root{
  --green-dark:#1f5a2b;
  --green-deep:#17451f;
  --green-bright:#59ff00;
  --green-lime:#82ff00;
  --green-soft:#b8ff75;
  --green-pale:#e3ffcb;
  --green-mist:#f4ffea;
  --ink:#1c1c1c;
  --muted:#555;
  --grey-bg:#f1f1f1;
  --white:#fff;
  --star:#f5b400;
}
*{box-sizing:border-box;margin:0;padding:0}
html,body{width:1200px;height:4136px;overflow:hidden}
body{font-family:'Poppins',sans-serif;color:var(--ink);background:var(--white);position:relative}
.btn{display:inline-block;background:var(--green-bright);color:var(--white);font-weight:600;font-size:17px;border-radius:30px;padding:14px 40px;text-decoration:none}
h2.section-title{font-size:44px;font-weight:700;text-align:center;color:var(--ink)}

/* header + hero */
.hero{position:absolute;left:0;top:0;width:1200px;height:820px;background:linear-gradient(180deg,#3f6f3a 0%,#8aa37a 45%,#cfd3c8 70%,#b9b2a4 100%)}
.hero-photo{position:absolute;inset:0;background:linear-gradient(160deg,rgba(40,90,40,.4),rgba(220,220,210,.2))}
.topbar{position:absolute;left:0;top:0;width:1200px;height:40px;background:var(--green-deep);color:var(--white);font-size:14px;display:flex;align-items:center;padding:0 70px;gap:30px}
.topbar span{display:flex;align-items:center;gap:8px}
.topbar .dot{width:14px;height:14px;border-radius:50%;background:var(--green-bright)}
.topbar .right{margin-left:auto;display:flex;gap:16px}
.topbar .right i{width:14px;height:14px;border:2px solid var(--white);border-radius:50%}
.navbar{position:absolute;left:0;top:40px;width:1200px;height:80px;background:rgba(31,90,43,.85);display:flex;align-items:center;padding:0 70px}
.brand{display:flex;align-items:center;gap:10px;color:var(--white);font-size:32px;font-weight:700}
.brand i{width:22px;height:22px;border-radius:50%;background:var(--green-bright)}
.nav-links{margin-left:auto;display:flex;gap:32px;color:var(--white);font-size:16px;font-weight:600}
.hero-copy{position:absolute;left:76px;top:340px;color:var(--white)}
.hero-copy h1{font-size:50px;font-weight:800;line-height:1.05;text-transform:uppercase;letter-spacing:1px}
.hero-copy p{font-size:36px;font-weight:500;line-height:1.2;margin:10px 0 40px}
.hero-products{position:absolute;left:560px;top:160px;width:560px;height:600px;border-radius:20px;background:linear-gradient(180deg,#2f6b33,#e9efe4);opacity:.85}

/* about */
.about{position:absolute;left:0;top:820px;width:1200px;height:720px;background:var(--white)}
.about-visual{position:absolute;left:80px;top:80px;width:460px;height:560px;border-radius:50% 50% 40% 40%;background:radial-gradient(circle at 50% 60%,var(--green-pale),var(--green-mist) 70%)}
.about-copy{position:absolute;left:610px;top:80px;width:520px}
.about-copy h2{font-size:44px;font-weight:700}
.about-copy .tagline{font-family:'Playball',cursive;font-size:34px;color:var(--green-dark);line-height:1.2;margin:6px 0 22px}
.about-copy p{font-size:15px;line-height:1.75;color:var(--muted);margin-bottom:18px}

/* ingredients */
.ingredients{position:absolute;left:0;top:1540px;width:1200px;height:520px;background:var(--green-pale)}
.ingredients h2{position:absolute;top:50px;width:100%}
.ing-visual{position:absolute;left:340px;top:180px;width:520px;height:340px;border-radius:260px 260px 0 0;background:radial-gradient(circle at 50% 100%,#f4c35c,#8ac348 45%,var(--green-soft) 75%)}
.ing-item{position:absolute;display:flex;align-items:center;gap:16px;font-size:18px;font-weight:600}
.ing-icon{width:70px;height:70px;border-radius:50%;background:var(--green-bright);display:flex;align-items:center;justify-content:center;flex:none}
.ing-line{position:absolute;border-top:2px dashed var(--green-dark)}

/* benefits */
.benefits{position:absolute;left:0;top:2060px;width:1200px;height:500px;background:var(--white)}
.benefits h2{position:absolute;top:40px;width:100%}
.benefit-row{position:absolute;left:70px;top:130px;width:1060px;display:flex;gap:28px}
.benefit-card{flex:1;height:300px;background:var(--green-pale);border-radius:20px;display:flex;flex-direction:column;align-items:center;justify-content:center;text-align:center;padding:0 26px;gap:24px;font-size:16px;font-weight:500;line-height:1.45}
.arrow{position:absolute;top:275px;font-size:32px;color:var(--ink)}

/* packages */
.packages{position:absolute;left:0;top:2560px;width:1200px;height:680px;background:var(--grey-bg)}
.packages h2{position:absolute;top:60px;width:100%}
.pack-row{position:absolute;left:70px;top:150px;width:1060px;display:flex;gap:32px}
.pack-card{flex:1;height:460px;background:var(--white);position:relative;text-align:center}
.pack-img{position:absolute;left:40px;top:30px;right:40px;height:260px;border-radius:10px;background:linear-gradient(180deg,#2b6a33,#cfe8b8)}
.pack-card h3{position:absolute;top:320px;width:100%;font-size:26px;font-weight:700}
.pack-card .price{position:absolute;top:360px;width:100%;font-size:24px;font-weight:500}
.pack-card .btn{position:absolute;top:395px;left:50%;transform:translateX(-50%);padding:10px 34px;font-size:15px}
.badge{position:absolute;right:0;top:0;width:56px;height:70px;background:var(--green-dark);color:var(--white);font-size:15px;font-weight:700;line-height:1.1;padding-top:10px;clip-path:polygon(0 0,100% 0,100% 100%,50% 82%,0 100%)}

/* testimonials */
.testimonials{position:absolute;left:0;top:3240px;width:1200px;height:460px;background:var(--white)}
.testimonials h2{position:absolute;top:40px;width:100%}
.t-photo{position:absolute;left:180px;top:140px;width:220px;height:220px;border-radius:50%;background:radial-gradient(circle,#d8c3a8,#7a9a64)}
.t-copy{position:absolute;left:460px;top:140px;width:560px}
.t-copy h4{font-size:20px;font-weight:700;display:flex;gap:14px;align-items:center}
.stars{color:var(--star);letter-spacing:3px;font-size:20px}
.t-copy p{font-size:16px;font-style:italic;line-height:1.6;color:var(--muted);margin:10px 0 14px}
.t-copy .name{color:var(--green-dark);font-weight:600;font-size:18px}

/* footer */
.footer{position:absolute;left:0;top:3700px;width:1200px;height:436px;background:var(--green-dark);color:var(--white)}
.footer .brand{position:absolute;left:70px;top:60px}
.footer-about{position:absolute;left:70px;top:150px;width:300px;font-size:14px;line-height:1.7}
.footer-col{position:absolute;top:40px}
.footer-col h5{font-size:24px;font-weight:600;margin-bottom:20px}
.links{display:grid;grid-template-columns:190px 120px;row-gap:12px;font-size:15px}
.sub-input{width:330px;height:50px;border-radius:26px;background:var(--white);color:#888;font-size:14px;padding:16px 24px;margin-bottom:14px}
.sub-btn{width:330px;height:50px;border-radius:26px;background:var(--green-bright);font-size:17px;font-weight:600;text-align:center;line-height:50px}
.footer-bar{position:absolute;left:70px;right:70px;top:340px;border-top:1px solid rgba(255,255,255,.3);padding-top:24px;display:flex;font-size:14px}
.social{margin-left:auto;display:flex;gap:22px}
.social i{width:22px;height:22px;border-radius:50%;background:var(--white)}
</style>
</head>
<body>

<section class="hero">
  <div class="hero-photo" role="img" aria-label="Background photo of green leaves over a pale wooden table"></div>
  <div class="topbar">
    <span><i class="dot"></i>1-800-555-0142</span>
    <span><i class="dot"></i>hello@leafwell-example.com</span>
    <div class="right"><i></i><i></i><i></i></div>
  </div>
  <nav class="navbar">
    <div class="brand"><i></i>Leafwell</div>
    <div class="nav-links"><span>Home</span><span>About Us</span><span>Benefits</span><span>Products Packages</span><span>Reviews</span><span>Blog</span><span>Contact Us</span></div>
  </nav>
  <div class="hero-products" role="img" aria-label="Three Verdant Vigor supplement bottles with fruits and vegetables"></div>
  <div class="hero-copy">
    <h1>Leafwell Verdant<br>Vigor</h1>
    <p>Verdant Vigor that is<br>100% vegan</p>
    <a class="btn">Shop Now</a>
  </div>
</section>

<section class="about">
  <div class="about-visual" role="img" aria-label="Supplement bottle with a fit couple standing in front of a pale green circle"></div>
  <div class="about-copy">
    <h2>About Verdant Vigor</h2>
    <div class="tagline">A Powerful Supplement for Getting<br>Optimal Health</div>
    <p>When healthy food is a nuisance, a weak immune system, the risk of chronic and mental illnesses in old age is quite common. According to one report of CDC, the majority of the US population is not able to get the necessary nutrients by a healthy diet alone! Therefore, you must take supplements to meet your nutrient needs.</p>
    <p>We present with you Verdant Vigor, a miracle supplement, a specific proprietary blend derived from a large number of herbs, fruits, and vegetables, and a lot of regular expected vitamins and minerals, for the need of optimal health.</p>
  </div>
</section>

<section class="ingredients">
  <h2 class="section-title">Ingredients</h2>
  <div class="ing-visual" role="img" aria-label="Supplement bottle rising from a heap of fresh fruits and vegetables"></div>
  <div class="ing-item" style="left:190px;top:160px">Nutrients in<br>one bottle<div class="ing-icon"><svg width="34" height="34" viewBox="0 0 34 34" fill="none" stroke="#1f5a2b" stroke-width="3"><rect x="9" y="8" width="16" height="22" rx="3"/><path d="M12 3h10v5H12z"/></svg></div></div>
  <div class="ing-item" style="left:785px;top:170px"><div class="ing-icon"><svg width="34" height="34" viewBox="0 0 34 34" fill="none" stroke="#1f5a2b" stroke-width="3"><circle cx="12" cy="12" r="6"/><circle cx="23" cy="22" r="7"/></svg></div>Minerals</div>
  <div class="ing-item" style="left:100px;top:345px">Essential<br>Vitamins<div class="ing-icon"><svg width="34" height="34" viewBox="0 0 34 34" fill="none" stroke="#1f5a2b" stroke-width="3"><rect x="5" y="12" width="24" height="10" rx="5" transform="rotate(-35 17 17)"/></svg></div></div>
  <div class="ing-item" style="left:900px;top:330px"><div class="ing-icon"><svg width="34" height="34" viewBox="0 0 34 34" fill="none" stroke="#1f5a2b" stroke-width="3"><circle cx="17" cy="19" r="10"/><path d="M17 9c0-4 3-6 6-6"/></svg></div>Proprietary<br>blend of 42<br>Fruits &amp;<br>Vegetables</div>
</section>

<section class="benefits">
  <h2 class="section-title">Benefits</h2>
  <span class="arrow" style="left:36px">&#8249;</span>
  <div class="benefit-row">
    <div class="benefit-card"><svg width="70" height="70" viewBox="0 0 70 70" fill="none" stroke="#222" stroke-width="3"><circle cx="35" cy="35" r="14"/><circle cx="35" cy="35" r="26" stroke-dasharray="6 6"/></svg>It May Help Increase Energy (ATP) and Regulate Metabolism</div>
    <div class="benefit-card"><svg width="70" height="70" viewBox="0 0 70 70" fill="none" stroke="#222" stroke-width="3"><circle cx="28" cy="30" r="16"/><circle cx="46" cy="44" r="13"/></svg>It May Help the Formation of Red Blood Cells</div>
    <div class="benefit-card"><svg width="70" height="70" viewBox="0 0 70 70" fill="none" stroke="#222" stroke-width="3"><circle cx="35" cy="35" r="18"/><path d="M35 5v12M35 53v12M5 35h12M53 35h12"/></svg>It May Help Strengthen the Immune System and Reduce Cancer and Heart Disease Risk</div>
    <div class="benefit-card"><svg width="70" height="70" viewBox="0 0 70 70" fill="none" stroke="#222" stroke-width="3"><path d="M20 48c-10-4-12-22 0-28 4-10 24-10 28 0 12 4 12 22 0 28-6 8-22 8-28 0z"/><path d="M35 18v34"/></svg>It May Help Improve Mental Health</div>
  </div>
  <span class="arrow" style="right:36px">&#8250;</span>
</section>

<section class="packages">
  <h2 class="section-title">Product Packages</h2>
  <div class="pack-row">
    <div class="pack-card"><div class="pack-img" role="img" aria-label="One supplement bottle"></div><h3>One Product</h3><div class="price">$34.95</div><a class="btn">Shop Now</a></div>
    <div class="pack-card"><div class="badge">10%<br>Off</div><div class="pack-img" role="img" aria-label="Two supplement bottles"></div><h3>Two Products</h3><div class="price">$31.45 each</div><a class="btn">Shop Now</a></div>
    <div class="pack-card"><div class="badge">20%<br>Off</div><div class="pack-img" role="img" aria-label="Three supplement bottles"></div><h3>Three Products</h3><div class="price">$27.95 each</div><a class="btn">Shop Now</a></div>
  </div>
</section>

<section class="testimonials">
  <h2 class="section-title">Testimonials</h2>
  <span class="arrow" style="left:120px;top:230px">&#8249;</span>
  <div class="t-photo" role="img" aria-label="Portrait photo of a smiling customer"></div>
  <div class="t-copy">
    <h4>Sed ut perspiciatis <span class="stars">★★★★★</span></h4>
    <p>" Natus error sit voluptatem accusantium doloremque laudantium, totam rem aperiam, eaque ipsa quae ab illo inventore veritatis et quasi architecto beatae vitae dicta sunt explicabo. Nemo enim ipsam voluptatem quia voluptas sit aspernatur aut odit aut fugit, sed quia consequuntur magni dolores eos. "</p>
    <div class="name">Name Heading</div>
  </div>
  <span class="arrow" style="right:120px;top:230px">&#8250;</span>
</section>

<footer class="footer">
  <div class="brand"><i></i>Leafwell</div>
  <p class="footer-about">Plant powered nutrition crafted with care, bringing vitamins, minerals and whole fruits and vegetables together in every daily serving.</p>
  <div class="footer-col" style="left:450px">
    <h5>Quick Links</h5>
    <div class="links"><span>Home</span><span>Reviews</span><span>About Us</span><span>Blog</span><span>Benefits</span><span>Contact Us</span><span>Products Packages</span></div>
  </div>
  <div class="footer-col" style="left:796px">
    <h5>Email Subscribe</h5>
    <div class="sub-input">Enter Email</div>
    <div class="sub-btn">Subscribe Now</div>
  </div>
  <div class="footer-bar">
    <span>2022 © Company Name. All Rights Reserved.</span>
    <div class="social"><i></i><i></i><i></i><i></i><i></i></div>
  </div>
</footer>

</body>
</html>
```